Webdesign für Steuerberaterin
Zielgruppe
Ich bin Steuerberaterin. Meine Zielgruppe sind sowohl Privatpersonen als auch Unternehmer sowie Männer und Frauen.
Aufgabenstellung
Bitte mein Logo und Foto mit berücksichtigen. Ich möchte keine Website, auf der alle 'Reiter' als eine Seite von oben nach unten durchlaufen. Sondern wirklich einzelne, voneinander getrennte Seiten.

```html
<!DOCTYPE html>
<html lang="de">
<head>
<meta charset="utf-8">
<title>Maren Brodtke – Steuerberaterin</title>
<link rel="stylesheet" href="https://fonts.googleapis.com/css2?family=Hind:wght@400;600;700&family=Montserrat:wght@400;500;600&family=Cormorant+Garamond:wght@500&display=swap">
<style>
  :root {
    --stage: #e9e9eb;
    --screen-top: #2a2b31;
    --screen-bottom: #1b1c21;
    --ink-light: #ffffff;
    --ink-muted: #8f97b3;
    --accent: #3fbf3a;
    --loss: #e0474c;
    --button-line: #4a4c55;
    --photo-deep: #1d4f86;
    --photo-light: #a9c3df;
    --device-frame: #0d0e12;
    --device-edge: #4b4d55;
    --app-bg: #252c48;
    --app-card: #313b5b;
    --app-row: #3d4869;
    --app-pill: #4a5578;
  }
  html, body {
    margin: 0;
    width: 1200px;
    height: 754px;
    overflow: hidden;
    background: var(--stage);
  }
  .page {
    position: absolute;
    left: 398px;
    top: 17px;
    width: 404px;
    height: 720px;
    overflow: hidden;
    background: linear-gradient(160deg, var(--screen-top) 0%, var(--screen-bottom) 100%);
    font-family: "Hind", sans-serif;
    color: var(--ink-light);
    box-shadow: 0 8px 30px rgba(0,0,0,0.18);
  }
  .brand {
    position: absolute;
    left: 20px;
    top: 52px;
    width: 140px;
    text-align: center;
    white-space: nowrap;
  }
  .brand-name {
    font-family: "Cormorant Garamond", serif;
    font-weight: 500;
    font-size: 18px;
    line-height: 1;
    color: var(--ink-light);
  }
  .brand-role {
    margin-top: 5px;
    font-family: "Cormorant Garamond", serif;
    font-size: 6px;
    letter-spacing: 1.2px;
    color: #cfd0d4;
  }
  .download-button {
    position: absolute;
    left: 197px;
    top: 26px;
    width: 162px;
    height: 40px;
    box-sizing: border-box;
    border: 1px solid var(--button-line);
    border-radius: 20px;
    color: var(--accent);
    font-size: 14px;
    letter-spacing: 0.3px;
    line-height: 41px;
    text-align: center;
  }
  .welcome {
    position: absolute;
    left: 0;
    top: 122px;
    width: 100%;
    margin: 0;
    text-align: center;
    font-weight: 700;
    font-size: 27px;
    line-height: 39px;
    white-space: nowrap;
  }
  .welcome .highlight { color: var(--accent); }
  .photo-strip {
    position: absolute;
    top: 404px;
    bottom: 0;
    width: 56px;
    background: linear-gradient(180deg, var(--photo-light) 0%, var(--photo-deep) 100%);
  }
  .photo-strip.left { left: 0; }
  .photo-strip.right { right: 0; }

  .app-device {
    position: absolute;
    left: 56px;
    top: 327px;
    width: 292px;
    bottom: 0;
    box-sizing: border-box;
    border: 3px solid var(--device-edge);
    border-bottom: none;
    border-radius: 34px 34px 0 0;
    background: var(--device-frame);
  }
  .device-camera {
    position: absolute;
    left: 94px; top: 36px;
    width: 6px; height: 6px;
    border-radius: 50%;
    background: #1e2a55;
  }
  .device-speaker {
    position: absolute;
    left: 119px; top: 37px;
    width: 46px; height: 4px;
    border-radius: 2px;
    background: #2b2c33;
  }
  .app-screen {
    position: absolute;
    left: 13px;
    top: 73px;
    width: 259px;
    bottom: 0;
    overflow: hidden;
    background: var(--app-bg);
    font-family: "Montserrat", sans-serif;
    color: var(--ink-light);
  }
  .status-dots {
    position: absolute;
    top: 4px;
    display: flex;
    gap: 3px;
  }
  .status-dots span {
    width: 6px; height: 5px; border-radius: 3px; background: var(--ink-light);
  }
  .status-dots.left { left: 22px; }
  .status-dots.left span { width: 7px; }
  .status-dots.right { right: 14px; }
  .app-bar-icon { position: absolute; top: 22px; }
  .app-title {
    position: absolute;
    top: 21px;
    left: 0; width: 100%;
    text-align: center;
    font-size: 9.5px;
    font-weight: 500;
    letter-spacing: 0.6px;
  }
  .app-card {
    position: absolute;
    left: 2px; right: 2px;
    top: 48px; bottom: 0;
    border-radius: 12px 12px 0 0;
    background: var(--app-card);
  }
  .small {
    position: absolute;
    font-size: 5px;
    letter-spacing: 0.5px;
    color: var(--ink-muted);
    white-space: nowrap;
  }
  .balance-amount {
    position: absolute;
    left: 20px; top: 32px;
    font-size: 11.5px;
    font-weight: 600;
    letter-spacing: 1.4px;
  }
  .balance-amount sup { font-size: 5px; letter-spacing: 0.5px; }
  .gain { color: var(--accent); }
  .add-bank {
    position: absolute;
    left: 147px; top: 32px;
    width: 89px; height: 16px;
    border-radius: 8px;
    background: var(--app-pill);
    font-size: 7px;
    font-weight: 500;
    letter-spacing: 0.5px;
    line-height: 17px;
    box-sizing: border-box;
    padding-left: 32px;
  }
  .add-bank .plus {
    position: absolute;
    left: 2px; top: 2px;
    width: 12px; height: 12px;
    border-radius: 50%;
    background: var(--ink-light);
  }
  .section-title {
    position: absolute;
    left: 20px;
    font-size: 8px;
    font-weight: 500;
    letter-spacing: 0.7px;
  }
  .total-pill {
    position: absolute;
    left: 188px; top: 77px;
    width: 48px; height: 12px;
    border-radius: 6px;
    background: var(--accent);
    font-size: 5.5px;
    font-weight: 600;
    letter-spacing: 0.4px;
    line-height: 12.5px;
    text-align: center;
  }
  .coin-row {
    position: absolute;
    left: 20px;
    width: 216px;
    height: 38px;
    border-radius: 3px;
    background: var(--app-row);
  }
  .coin-icon {
    position: absolute;
    left: 13px; top: 10px;
    width: 18px; height: 18px;
    border-radius: 2px;
    background: #6f7895;
  }
  .coin-icon.bright { background: var(--ink-light); }
  .coin-name {
    position: absolute;
    left: 55px; top: 10px;
    font-size: 5.5px;
    font-weight: 600;
    letter-spacing: 0.4px;
  }
  .coin-value {
    position: absolute;
    right: 13px; top: 10px;
    font-size: 5px;
    letter-spacing: 0.4px;
  }
  .coin-row .small.units { left: 55px; top: 21px; }
  .coin-row .small.change { right: 13px; top: 21px; }
  .small.change.up { color: var(--accent); }
  .small.change.down { color: var(--loss); }
</style>
</head>
<body>
  <main class="page">
    <header>
      <div class="brand">
        <div class="brand-name">Maren Brodtke</div>
        <div class="brand-role">STEUERBERATERIN</div>
      </div>
      <div class="download-button">DOWNLOAD</div>
    </header>

    <h1 class="welcome">
      <span class="highlight">Schön,</span> dass <span class="highlight">Sie</span> da sind!<br>
      Ich freue mich, dass Sie den<br>
      Weg zu mir gefunden haben!
    </h1>

    <div class="photo-strip left" role="img" aria-label="Foto: Finanzdiagramme in Blautönen"></div>
    <div class="photo-strip right" role="img" aria-label="Foto: Finanzdiagramme und Münzen in Blautönen"></div>

    <section class="app-device" aria-label="Smartphone mit Finanz-App">
      <div class="device-camera"></div>
      <div class="device-speaker"></div>

      <div class="app-screen">
        <div class="status-dots left"><span></span><span></span></div>
        <div class="status-dots right"><span></span><span></span><span></span></div>

        <svg class="app-bar-icon" style="left:22px" width="13" height="9" viewBox="0 0 13 9">
          <path d="M0 1h13M2 4.5h11M4 8h9" stroke="#ffffff" stroke-width="1.2"/>
        </svg>
        <div class="app-title">My Money</div>
        <svg class="app-bar-icon" style="left:227px" width="13" height="11" viewBox="0 0 13 11">
          <path d="M2 8.5h9M3 8.5V5a3.5 3.5 0 0 1 7 0v3.5M5.5 10h2" stroke="#ffffff" stroke-width="1.1" fill="none"/>
          <circle cx="10.5" cy="2" r="1.8" fill="#e0474c"/>
        </svg>

        <div class="app-card">
          <div class="small" style="left:20px; top:24px">Balance ›</div>
          <div class="balance-amount">$15.496.<sup>29</sup></div>
          <div class="small gain" style="left:20px; top:51px">+ 5.25 % ▲</div>
          <div class="add-bank"><span class="plus"></span>Add Bank</div>

          <div class="section-title" style="top:78px">Steuer</div>
          <div class="small" style="left:130px; top:81px">TOTAL AMOUNT</div>
          <div class="total-pill">$695.79</div>

          <div class="coin-row" style="top:101px">
            <div class="coin-icon"></div>
            <div class="coin-name">Nordcoin (NRC)</div>
            <div class="coin-value">$5.610.66</div>
            <div class="small units">0.00612</div>
            <div class="small change up">+ $79.82 (2.5%) ▲</div>
          </div>
          <div class="coin-row" style="top:146px">
            <div class="coin-icon bright"></div>
            <div class="coin-name">Aurum (AUR)</div>
            <div class="coin-value">$69.84</div>
            <div class="small units">9.58712</div>
            <div class="small change up">+ $4.09 (0.6%) ▲</div>
          </div>

          <div class="section-title" style="top:197px">Other Coins</div>
          <div class="small" style="left:206px; top:200px">View All ›</div>

          <div class="coin-row" style="top:215px">
            <div class="coin-icon"></div>
            <div class="coin-name">Lumen (LMN)</div>
            <div class="coin-value">$32.82</div>
            <div class="small units">0.249</div>
            <div class="small change down">- $74.82 (6%) ▼</div>
          </div>
          <div class="coin-row" style="top:261px"></div>
        </div>
      </div>
    </section>
  </main>
</body>
</html>
```